Super elegant, crisp & clean Business card design required

We recently upgraded our branding - which is on our website - talvendoraphoto.com

I would like a simple, yet elegant, clean business card design please.

The font of my logo is Cinzel - and because of the natural colour - it's best to have this on a black background.

I would like to have the back of the business card - with simply my logo.

PLEASE DO NOT SUBMIT A COMPLICATED / UNCLEAN DESIGN

Industry/Entity Type

Business

Contact Information for Business Card

Talven Doroshko Photography

Font styles to use
Other font styles liked:
• Cinzel

Requirements
Must have
• A backpage with nothing but my logo
• Simple design - stands out
Should not have
• Colour that dont align with my logo
• Over complicated '/ non symmetrical design

```html
<!DOCTYPE html>
<html lang="en">
<head>
<meta charset="utf-8">
<title>Talven Doroshko Photography — Business Card</title>
<link rel="stylesheet" href="https://fonts.googleapis.com/css2?family=Cinzel:wght@400;600&display=swap">
<style>
  :root {
    --backdrop: #b1b1b1;
    --card-dark: #121315;
    --card-dark-edge: #0c0d0f;
    --card-light: #f3f3f3;
    --card-light-shade: #e2e2e2;
    --gold: #7b6b56;
    --gold-soft: #6a5d4c;
    --ink-grey: #77716a;
  }
  * { margin: 0; padding: 0; box-sizing: border-box; }
  html, body { width: 1200px; height: 1050px; overflow: hidden; }
  body {
    background: var(--backdrop);
    font-family: "Cinzel", "Times New Roman", serif;
    position: relative;
  }
  .card { position: absolute; }

  /* Back of card */
  .card-back {
    left: 86px; top: 483px; width: 630px; height: 359px;
    background: radial-gradient(ellipse at 50% 45%, #1a1b1e 0%, var(--card-dark) 60%, var(--card-dark-edge) 100%);
  }
  .brand {
    position: absolute; left: 0; right: 0;
    text-align: center; color: var(--gold);
    font-weight: 400;
  }
  .brand-mark {
    display: block; margin: 0 auto 14px;
    width: 58px; height: 58px; border-radius: 50%;
    border: 1.5px solid var(--gold);
  }
  .card-back .brand { top: 112px; font-size: 20px; letter-spacing: 0.5px; line-height: 1.2; }
  .card-back .brand-name { display: block; }

  /* Front of card */
  .card-front {
    left: 746px; top: 214px; width: 359px; height: 630px;
    background: linear-gradient(180deg, var(--card-light) 0%, #ececec 55%, var(--card-light-shade) 100%);
  }
  .card-front .brand { top: 56px; font-size: 17px; line-height: 1.25; }
  .card-front .brand-mark { width: 64px; height: 64px; margin-bottom: 20px; }

  .person {
    position: absolute; left: 0; right: 0; top: 312px;
    text-align: center;
  }
  .person-name {
    font-size: 20px; font-weight: 600; color: var(--gold-soft);
    letter-spacing: 0.3px;
  }
  .person-role {
    font-size: 14px; color: var(--ink-grey); margin-top: 2px;
  }

  .contact {
    position: absolute; left: 0; right: 0; top: 463px;
    text-align: center; list-style: none;
    font-size: 13.5px; color: var(--ink-grey); line-height: 18.5px;
  }
  .contact .email { font-size: 12.5px; }
  .website {
    position: absolute; left: 0; right: 0; top: 558px;
    text-align: center; font-size: 12.5px; color: var(--ink-grey);
  }
</style>
</head>
<body>

  <section class="card card-back" aria-label="Back of business card">
    <div class="brand">
      <span class="brand-mark" aria-hidden="true"></span>
      <span class="brand-name">Talven Doroshko Photography</span>
    </div>
  </section>

  <section class="card card-front" aria-label="Front of business card">
    <div class="brand">
      <span class="brand-mark" aria-hidden="true"></span>
      <span class="brand-name">Talven Doroshko<br>Photography</span>
    </div>

    <div class="person">
      <p class="person-name">Talven Doroshko</p>
      <p class="person-role">Photographer</p>
    </div>

    <ul class="contact">
      <li>T : 1800 417 390</li>
      <li>M : 07 912 508 364</li>
      <li class="email">E : info@talvendoraphoto.com</li>
    </ul>

    <p class="website">www.talvendoraphoto.com</p>
  </section>

</body>
</html>
```